KDWB Business Card

Looking for a business card design to incorporate our branding. We want to only use the colors listing in the Branding Package (attached).
Updates

Target Market(s)

People who need their phone or device fixed.

Industry/Entity Type

Electronics

Contact Information for Business Card

Please use:

Brightwick Gadget Clinic LLC
4810 E Harlow Ridge Rd
Suite 417
San Antonio, TX 78163

Marcus Delgrove, Store Manager

(210) 555-0147

Requirements
Must have
• Must include the colors that are contained within the Branding Package PDF file.

```html
<!DOCTYPE html>
<html lang="en">
<head>
<meta charset="utf-8">
<title>Brightwick Gadget Clinic – Business Card</title>
<link rel="stylesheet" href="https://fonts.googleapis.com/css2?family=Roboto:wght@300;400&display=swap">
<style>
  :root {
    --stage: #eeebe6;
    --card-dark: #4b4d4f;
    --card-light: #f7f7f7;
    --brand-orange: #e8601c;
    --text-light: #ffffff;
    --text-muted: #d9d9d9;
    --text-dark: #4b4d4f;
  }
  * { margin: 0; padding: 0; box-sizing: border-box; }
  html, body {
    width: 1200px; height: 892px; overflow: hidden;
    background: var(--stage);
    font-family: "Roboto", Arial, sans-serif;
    font-weight: 300;
  }
  .card-sheet {
    width: 1200px; height: 892px;
    display: flex; align-items: center; justify-content: center; gap: 40px;
  }
  .card {
    position: relative;
    width: 540px; height: 309px;
    border-radius: 3px;
    box-shadow: 0 10px 24px rgba(0,0,0,.18);
  }
  .card--front { background: var(--card-dark); color: var(--text-light); }
  .card--back { background: var(--card-light); color: var(--text-dark); }

  .brand {
    display: flex; align-items: center; gap: 12px;
  }
  .brand__mark {
    width: 36px; height: 36px;
    background: var(--brand-orange);
    border-radius: 4px;
  }
  .brand__name {
    color: var(--brand-orange);
    font-size: 27px; font-weight: 300; letter-spacing: .3px;
  }

  .card--front .brand { position: absolute; left: 46px; top: 52px; }

  .contact { position: absolute; left: 202px; top: 132px; }
  .contact__name { font-size: 27px; font-weight: 300; line-height: 1.05; }
  .contact__role { font-size: 14px; color: var(--text-muted); margin-top: 3px; }
  .contact__phone { font-size: 14px; color: var(--text-muted); margin-top: 22px; }

  .address {
    position: absolute; left: 46px; bottom: 34px;
    font-size: 14px; color: var(--text-muted); letter-spacing: .2px;
  }

  .card--back .brand { position: absolute; right: 48px; top: 120px; }
  .website {
    position: absolute; left: 46px; bottom: 36px;
    font-size: 19px; color: var(--text-dark); letter-spacing: .3px;
  }
</style>
</head>
<body>
  <main class="card-sheet">
    <section class="card card--front" aria-label="Business card front">
      <div class="brand">
        <span class="brand__mark"></span>
        <span class="brand__name">Brightwick Gadget Clinic</span>
      </div>
      <div class="contact">
        <p class="contact__name">Marcus Delgrove</p>
        <p class="contact__role">Store Manager</p>
        <p class="contact__phone">(210) 555-0147</p>
      </div>
      <p class="address">4810 E Harlow Ridge Rd, Suite 417, San Antonio, TX 78163</p>
    </section>

    <section class="card card--back" aria-label="Business card back">
      <div class="brand">
        <span class="brand__mark"></span>
        <span class="brand__name">Brightwick Gadget Clinic</span>
      </div>
      <p class="website">www.BrightwickGadget.com</p>
    </section>
  </main>
</body>
</html>
```